My name is Delia Okonkwo,I want to create a web page for my personal dog grooming business. The name on the web page can be "Delia's Dog Grooming" I am located in San Antonio Texas. The page would help grow my customer base. Before and after pictures would display the quality of work that I do. On my page I can provide information about myself, my services, and pricing.
Updates

I have updated project to guaranteed pay

Please try to incorporate a schnauzer in an icon or logo. My dog is a schnauzer. THANKS!!!!!!!!!!!!

Target Market(s)

Dog Owners

Industry/Entity Type

Business

Requirements
Must have
• -A spot for before and after pictures.
-An about me section
-A section to make an appointment
Nice to have
• My favorite Color is purple. I think different shades of purple would be nice or purple with a light green

please incorporate a schnauzer in any icon or logo. My dog is a schnauzer.

```html
<!DOCTYPE html>
<html lang="en">
<head>
<meta charset="utf-8">
<title>Delia's Dog Grooming</title>
<link rel="stylesheet" href="https://fonts.googleapis.com/css2?family=PT+Sans:ital,wght@0,400;0,700;1,400;1,700&family=PT+Sans+Narrow:wght@700&family=Roboto+Condensed:wght@300;400&display=swap">
<style>
:root{
  --purple-deep:#3d0a5c;
  --purple:#6a1f96;
  --purple-bright:#8b3cc0;
  --purple-text:#5a1a7a;
  --lilac:#b77ad6;
  --green:#9bd21e;
  --green-dark:#5fa10a;
  --ink:#2a2a2a;
  --grey-line:#d9d9d9;
  --white:#fff;
  --fur-dark:#3b3b3d;
  --fur-mid:#6a6a6c;
  --floor:#e4e4e6;
}
*{box-sizing:border-box;margin:0;padding:0}
html,body{width:942px;height:1200px;overflow:hidden}
body{position:relative;background:#f2f2f4;font-family:Arial,Helvetica,sans-serif;color:var(--ink)}
.abs{position:absolute}
.top-band{left:0;top:0;width:942px;height:350px;background:radial-gradient(ellipse at 50% 0%,var(--purple-bright),var(--purple) 45%,var(--purple-deep))}
.body-bg{left:0;top:350px;width:942px;height:747px;background:linear-gradient(#fafafa,#eeeef0)}
.footer{left:0;top:1097px;width:942px;height:103px;background:linear-gradient(var(--purple),var(--purple-deep));color:var(--white);font-size:11px}
.footer .copy{position:absolute;left:38px;top:40px;line-height:15px}
.footer .links{position:absolute;right:38px;top:47px;word-spacing:2px}

.brand-mark{left:38px;top:17px;width:112px;height:112px;border-radius:50%;border:5px solid #d8d2de;background:radial-gradient(circle at 45% 40%,#ffffff,#e6e2ea 60%,#b9b3c0)}
.brand-name{left:162px;top:44px;font-family:"PT Sans",sans-serif;font-weight:700;line-height:1}
.brand-name .big{display:block;font-size:40px;letter-spacing:.5px;color:var(--green)}
.brand-name .small{display:block;font-size:17px;margin-top:5px;margin-left:18px;letter-spacing:.5px;color:var(--green)}

.call-photo{left:632px;top:4px;width:88px;height:80px;border-radius:40px 40px 6px 6px;background:radial-gradient(ellipse at 50% 35%,#ffffff,#efeeee 50%,#c9c8c8)}
.call{left:725px;top:16px;color:var(--white);font-family:"PT Sans",sans-serif;font-weight:700;line-height:1}
.call .label{font-size:17px}
.call .num{font-size:30px;margin-top:2px}

.nav{left:384px;top:85px;width:521px;height:37px;border-radius:9px;background:linear-gradient(#fff,#dcdcdc);display:flex;align-items:center;justify-content:space-around;font-family:"PT Sans",sans-serif;font-size:16px;color:#222;padding:0 8px}
.nav span.sep{width:1px;height:16px;background:#aaa}

.slider{left:37px;top:142px;width:867px;height:283px;border-radius:10px;background:linear-gradient(#fff,#e9e9e9 70%,#d2d2d2);border:3px solid #eee;box-shadow:0 14px 16px -10px rgba(0,0,0,.35);overflow:hidden}
.slide-photo{position:absolute;left:0;top:0;width:861px;height:277px;background:
  radial-gradient(ellipse 200px 120px at 290px 180px,var(--fur-dark),rgba(59,59,61,.85) 60%,rgba(59,59,61,0) 100%),
  radial-gradient(ellipse 190px 125px at 680px 175px,#4a4847,rgba(80,78,76,.85) 60%,rgba(80,78,76,0) 100%),
  linear-gradient(#fafafa,#f0f0f0 55%,var(--floor) 80%,#d4d4d4)}
.arrow{position:absolute}

.share-bar{left:37px;top:461px;width:867px;height:67px;border-radius:10px;background:linear-gradient(#fafafa,#ececec);border:1px solid var(--grey-line)}
.share-bar .label{position:absolute;left:16px;top:22px;font-family:"PT Sans",sans-serif;font-size:18px;color:#333}
.share-bar .dots{position:absolute;left:175px;top:18px;display:flex;gap:7px}
.share-bar .dots i{display:block;width:30px;height:30px;border-radius:50%;border:2px solid #fff;box-shadow:0 1px 3px rgba(0,0,0,.35);background:radial-gradient(circle at 40% 35%,#b98ad6,var(--purple))}
.btn-call{position:absolute;left:615px;top:13px;width:221px;height:42px;border-radius:10px;background:linear-gradient(#c4f03e,var(--green) 50%,var(--green-dark));box-shadow:0 3px 4px rgba(0,0,0,.3);font-family:"PT Sans Narrow",sans-serif;font-weight:700;font-size:21px;color:#1f2a08;text-align:center;line-height:42px;letter-spacing:.6px}

.card{border:2px solid var(--lilac);border-radius:8px;background:rgba(244,244,246,.95);box-shadow:0 0 0 4px #ececee}
.card h2{font-family:"Roboto Condensed",sans-serif;font-weight:400;color:var(--purple-text);line-height:1}
.card h2 .pre{font-size:22px;font-weight:300}
.card h2 .main{font-size:31px}
.lines{font-size:13px;color:var(--ink)}
.lines span{display:block;text-align:justify;text-align-last:justify;white-space:nowrap}
.lines span.last{text-align-last:left}
.more{color:var(--purple-text);font-style:italic;text-decoration:underline;margin-left:6px}

.welcome{left:40px;top:545px;width:418px;height:206px;padding:11px 12px}
.welcome h2 .main{display:block;margin-top:3px}
.welcome .lines{margin-top:8px;line-height:18.6px}
.welcome .lines span{word-spacing:0}

.gallery{left:483px;top:545px;width:418px;height:206px;padding:11px 12px}
.gallery h2 .main{display:block;margin-top:3px}
.thumb{position:absolute;top:83px;width:148px;height:103px;border-radius:7px;border:3px solid #e6e6e6;box-shadow:0 2px 4px rgba(0,0,0,.35);overflow:hidden}
.thumb.before{background:radial-gradient(ellipse 60px 40px at 55% 45%,#3c3c3e,rgba(60,60,62,0)),linear-gradient(#e9e9e9,#c8c8c8)}
.thumb.after{background:radial-gradient(ellipse 60px 40px at 50% 50%,#2e2e30,rgba(46,46,48,0)),linear-gradient(#9bb08a,#d8d8d8)}
.thumb span{position:absolute;left:0;bottom:0;width:100%;height:22px;background:rgba(30,30,30,.85);color:#fff;font-size:12px;font-weight:700;text-align:center;line-height:22px}

.about{left:40px;top:772px;width:566px;height:205px;padding:12px 12px}
.about h2 .pre{font-size:24px}
.about-photo{position:absolute;left:12px;top:56px;width:134px;height:114px;background:linear-gradient(90deg,#d9a57e,#b9876a 40%,#4d4d4f 65%,#5e5e60)}
.about .lines{position:absolute;left:162px;top:52px;width:390px;line-height:21.4px}

.testimonial{left:632px;top:773px;width:268px;height:267px;padding:14px 12px}
.testimonial h2 .pre{font-size:22px}
.client-photo{position:absolute;left:13px;top:58px;width:78px;height:79px;border:4px solid #fff;box-shadow:0 1px 4px rgba(0,0,0,.35);background:linear-gradient(#f6efe6,#ead4bf 45%,#8a7c70)}
.testimonial .p1{position:absolute;left:100px;top:56px;width:148px;line-height:18.6px}
.testimonial .p2{position:absolute;left:12px;top:144px;width:244px;line-height:18.6px}
.testimonial .foot{position:absolute;left:12px;top:206px;width:244px;font-size:12px}
.testimonial .by{position:absolute;right:0;top:0;color:var(--purple-text)}
.testimonial .foot .more{position:absolute;left:0;top:16px;margin:0;font-size:13px}
.testimonial .when{position:absolute;right:0;top:16px;font-style:italic;color:#333}
.testimonial .when b{font-style:normal;font-weight:400;color:var(--purple-text);margin-left:4px}

.offer{left:37px;top:999px;width:572px;height:72px;border-radius:10px;border:1px solid #7fb31a;background:linear-gradient(#d6fb5a,var(--green) 55%,#7cc012)}
.offer-photo{position:absolute;left:22px;top:-9px;width:90px;height:90px;border-radius:50%;border:4px solid #fff;background:radial-gradient(circle at 50% 45%,#d9d9d9,#8a8a8a 45%,#3e3e40);box-shadow:0 2px 5px rgba(0,0,0,.4)}
.offer-text{position:absolute;left:121px;top:5px;width:370px;text-align:center;font-family:"PT Sans",sans-serif;font-weight:700;font-size:17.5px;line-height:21.5px;color:var(--purple-text)}
.offer-text em{font-size:19px}
.offer-link{position:absolute;right:10px;top:47px;font-family:"PT Sans",sans-serif;font-weight:700;font-size:14px;color:#222;text-decoration:underline}
</style>
</head>
<body>
<div class="abs top-band"></div>
<div class="abs body-bg"></div>

<header>
  <div class="abs brand-mark"></div>
  <div class="abs brand-name"><span class="big">DELIA'S</span><span class="small">DOG GROOMING</span></div>
  <div class="abs call-photo" role="img" aria-label="Photo of a white dog wearing a telephone headset"></div>
  <div class="abs call"><div class="label">Call Us:</div><div class="num">021 5550147</div></div>
  <nav class="abs nav">
    <span>Home</span><span class="sep"></span><span>About Me</span><span class="sep"></span><span>Services</span><span class="sep"></span><span>Grooming</span><span class="sep"></span><span>Gallery</span><span class="sep"></span><span>Contact Me</span>
  </nav>
</header>

<section class="abs slider">
  <div class="slide-photo" role="img" aria-label="Photo of two schnauzers lying on a white tiled floor"></div>
  <svg class="arrow" style="left:12px;top:124px" width="26" height="46" viewBox="0 0 26 46"><polyline points="22,3 5,23 22,43" fill="none" stroke="#777" stroke-width="4" stroke-linecap="round"/></svg>
  <svg class="arrow" style="right:12px;top:124px" width="26" height="46" viewBox="0 0 26 46"><polyline points="4,3 21,23 4,43" fill="none" stroke="#777" stroke-width="4" stroke-linecap="round"/></svg>
</section>

<section class="abs share-bar">
  <span class="label">Share with us on:</span>
  <div class="dots"><i></i><i></i><i></i><i></i><i></i></div>
  <div class="btn-call">Call For Appointment</div>
</section>

<section class="abs card welcome">
  <h2><span class="pre">Welcome to</span><span class="main">Delia's Dog Grooming</span></h2>
  <div class="lines">
    <span>Architecto beatae naseaeraciat kuiase undeosler miasosac usa</span>
    <span>ntuedearsteked icexplic abo nemo enim ipsam lertasevol</span>
    <span>uptatemia voluptas sit. Aspernatur aut odit aut fugitedera quia</span>
    <span>consequuntur magni dolores eosqui ratione voluptatem. Fequi</span>
    <span>nesciunt neque porro quisquam estqui dolorem ipsumquia dolor</span>
    <span class="last">sitamet. <span class="more" style="display:inline">Read More</span></span>
  </div>
</section>

<section class="abs card gallery">
  <h2><span class="pre">View our</span><span class="main">Grooming Gallery</span></h2>
  <svg class="arrow" style="left:12px;top:113px" width="24" height="44" viewBox="0 0 24 44"><polyline points="20,3 5,22 20,41" fill="none" stroke="#888" stroke-width="4" stroke-linecap="round"/></svg>
  <div class="thumb before" style="left:50px" role="img" aria-label="Schnauzer before grooming"><span>Before</span></div>
  <div class="thumb after" style="left:218px" role="img" aria-label="Schnauzer after grooming"><span>After</span></div>
  <svg class="arrow" style="right:12px;top:113px" width="24" height="44" viewBox="0 0 24 44"><polyline points="4,3 19,22 4,41" fill="none" stroke="#888" stroke-width="4" stroke-linecap="round"/></svg>
</section>

<section class="abs card about">
  <h2><span class="pre">About </span><span class="main">My Self</span></h2>
  <div class="about-photo" role="img" aria-label="Photo of the groomer holding her schnauzer"></div>
  <div class="lines">
    <span>Architecto beatae naseaeraciat kuiase undeosler miasosac usa</span>
    <span>ntuedearsteked icexplic abo nemo enim ipsam lertasevol</span>
    <span>uptatemia voluptas sit. Aspernatur aut odit aut fugitedera quia</span>
    <span>consequuntur magni dolores eosqui ratione voluptatem. Fequi</span>
    <span>nesciunt neque porro quisquam estqui dolorem ipsumquia dolor</span>
    <span class="last">sitamet. <span class="more" style="display:inline">Read More</span></span>
  </div>
</section>

<section class="abs card testimonial">
  <h2><span class="pre">Client's </span><span class="main">Testimonials</span></h2>
  <div class="client-photo" role="img" aria-label="Photo of a client with her small dog"></div>
  <div class="lines p1">
    <span class="last">Architecto beatae nase-</span>
    <span class="last">aeraciat kuiase undeosler</span>
    <span class="last">miasosac usa ntuedea</span>
    <span class="last">rsteked icexplic abo nemo</span>
  </div>
  <div class="lines p2">
    <span>ipsam lertasevol uptatemia voluptas sit.</span>
    <span>Aspernatur aut odit aut fugitedera quia con-</span>
    <span class="last">sequuntur magni....</span>
  </div>
  <div class="foot"><span class="by">By</span><span class="more">Read More</span><span class="when">3 days ago <b>Maren Holt</b></span></div>
</section>

<section class="abs offer">
  <div class="offer-photo" role="img" aria-label="Round photo of a smiling schnauzer"></div>
  <div class="offer-text">Special Offers for Dog's in<br>Delia's Dog Grooming. <em>FLAT 50% Off</em><br>on first five Customers !</div>
  <span class="offer-link">Click Here</span>
</section>

<footer class="abs footer">
  <div class="copy">Copyright © 2012 by Delia's Dog Grooming<br>All Right Reserved</div>
  <div class="links">Home | About Me | Services | Grooming | Gallery | Contact Me</div>
</footer>
</body>
</html>
```